New Innovative Counselling and psychotherapy Service needs Business Card design

Keep it simple and professional. On one side, just company name and logo (perhaps in all blue) and maybe a tag line.

On other side (all white) my name and Qualifications in centre

Industry/Entity Type

Health And Wellness

Contact Information for Business Card

Dara Whelby
Counsellor & Psychotherapist
BSc (Psychol.), BA, Dip. (Couns. & Psych.), PG.Cert (CBT), FGTrK, ONRE

I will also require Mobile no, Email and web site address of which I'll pass on to final designer.

Font styles to use
Sans Serif

Requirements
Must have
• My Logo Only and please use the colours in logo that is in it.
Should not have
• Any other images

```html
<!DOCTYPE html>
<html lang="en">
<head>
<meta charset="utf-8">
<title>Kestrel Lane – Business Card</title>
<link href="https://fonts.googleapis.com/css2?family=Raleway:wght@400&family=Lato:ital,wght@0,400;1,400&family=Cormorant+Garamond:ital,wght@1,600&display=swap" rel="stylesheet">
<style>
  :root {
    --bg: #2b2b2b;
    --paper: #ffffff;
    --ink: #231f20;
    --ink-soft: #3a3a3a;
    --blue: #42b0ea;
    --green: #8fd152;
    --rule: #b9b9b9;
    --white: #ffffff;
  }
  * { margin: 0; padding: 0; box-sizing: border-box; }
  html, body { width: 1200px; height: 1200px; overflow: hidden; }
  body { background: var(--bg); position: relative; font-family: "Lato", sans-serif; }

  .card {
    position: absolute;
    top: 310px;
    width: 364px;
    height: 594px;
    box-shadow: 0 3px 8px rgba(0,0,0,.45);
  }
  .card--front { left: 234px; background: var(--paper); }
  .card--back {
    left: 627px; width: 369px;
    background:
      radial-gradient(circle at 50% 42%, rgba(66,176,234,.85) 0, rgba(66,176,234,0) 60%),
      linear-gradient(160deg, #55c0d6 0%, #6aaed0 30%, #49b2e6 55%, #8fd152 85%, #9bd55a 100%);
    overflow: hidden;
  }
  .card__decor {
    position: absolute; inset: 0;
    background: radial-gradient(ellipse 70% 45% at 50% 40%, rgba(255,255,255,.12), rgba(255,255,255,0) 70%);
  }

  .brand { position: absolute; left: 0; right: 0; text-align: center; }
  .brand__dot {
    position: absolute; top: 84px; left: 126px;
    width: 112px; height: 112px; border-radius: 50%;
    background: var(--blue);
  }
  .brand__name {
    position: absolute; top: 224px; left: 0; right: 0; text-align: center;
    font-family: "Raleway", sans-serif; font-weight: 400;
    font-size: 34px; color: var(--ink); letter-spacing: -.3px;
  }

  .person { position: absolute; top: 338px; left: 0; right: 0; text-align: center; }
  .person__name { font-size: 22px; line-height: 26px; font-weight: 400; letter-spacing: .2px; }
  .person__name .first { color: var(--blue); }
  .person__name .last { color: var(--green); }
  .person__role { font-size: 16px; line-height: 20px; color: var(--ink-soft); }
  .person__quals { font-size: 16px; line-height: 22px; font-style: italic; color: var(--ink-soft); margin-top: 3px; }

  .contact-rule {
    position: absolute; top: 447px; left: 87px; width: 190px; height: 26px;
    display: flex; align-items: center; justify-content: center; gap: 3px;
  }
  .contact-rule::before, .contact-rule::after {
    content: ""; flex: 1; height: 1px; background: var(--rule);
  }
  .contact-rule svg { width: 24px; height: 24px; display: block; }

  .contact {
    position: absolute; top: 484px; left: 0; right: 0; text-align: center;
    font-size: 16px; line-height: 22px; color: var(--ink); list-style: none;
  }

  .tagline {
    position: absolute; top: 160px; left: 0; right: 0; text-align: center;
    font-family: "Cormorant Garamond", serif; font-style: italic; font-weight: 600;
    font-size: 40px; line-height: 67px; color: var(--white);
  }

  .social {
    position: absolute; top: 522px; left: 45px; right: 45px;
    display: flex; align-items: center; gap: 8px;
    font-size: 11px; color: var(--white); letter-spacing: .3px; white-space: nowrap;
  }
  .social::before, .social::after {
    content: ""; flex: 1; height: 1px; background: rgba(255,255,255,.55);
  }
</style>
</head>
<body>

<section class="card card--front" aria-label="Business card front">
  <div class="brand">
    <span class="brand__dot" aria-hidden="true"></span>
    <p class="brand__name">Kestrel Lane</p>
  </div>

  <div class="person">
    <h1 class="person__name"><span class="first">DARA</span> <span class="last">WHELBY</span></h1>
    <p class="person__role">Counsellor &amp; Psychotherapist</p>
    <p class="person__quals">BSc (Psychol.), BA, Dip. (Couns. &amp; Psych.),<br>PG.Cert (CBT), FGTrK, ONRE</p>
  </div>

  <div class="contact-rule" aria-hidden="true">
    <svg viewBox="0 0 24 24"><circle cx="12" cy="12" r="12" fill="#42b0ea"/><path d="M7 9.5c0-1.2 2.2-2.2 5-2.2s5 1 5 2.2v1h-2.2v-1.2h-5.6v1.2H7z M8.5 11.5h7l1 5h-9z" fill="#fff"/></svg>
    <svg viewBox="0 0 24 24"><circle cx="12" cy="12" r="12" fill="#42b0ea"/><rect x="6.5" y="8" width="11" height="8" rx="1" fill="#fff"/><path d="M6.8 8.4 12 12.6l5.2-4.2" stroke="#42b0ea" stroke-width="1.2" fill="none"/></svg>
    <svg viewBox="0 0 24 24"><circle cx="12" cy="12" r="12" fill="#42b0ea"/><circle cx="12" cy="12" r="5.8" fill="none" stroke="#fff" stroke-width="1.4"/><path d="M12 6.2v11.6M6.2 12h11.6M12 6.2c-2.6 3-2.6 8.6 0 11.6M12 6.2c2.6 3 2.6 8.6 0 11.6" stroke="#fff" stroke-width="1" fill="none"/></svg>
  </div>

  <ul class="contact">
    <li>085 2390 417</li>
    <li>hello@kestrellane.com</li>
    <li>www.kestrellane.com</li>
  </ul>
</section>

<section class="card card--back" aria-label="Business card back">
  <div class="card__decor" role="img" aria-label="Soft blue and green brand gradient"></div>
  <p class="tagline">Caring For Your<br>Psychological<br>Well-Being Is<br>Our Top Priority</p>
  <p class="social">Kinloop · Pinmoor · Trillet · Glimora</p>
</section>

</body>
</html>
```